Letterhead for a German Distribution/Manufacturing Company

We need a professional Letterhead in a unique Design.
not to playful.
The Letterhead has to show show that we are a international company with headquater in Germany.
all details like adress, Vat Tax Number, Bank Accout, Eori, email, Company number has to be on the Letterhead.
for example use: VAT TAX DE5470318 Bank Account: Kestrel Bank IBAN DE412058731ß204683 Swift: MORV0417352 EORI 3150428697 Company Number: HRB 51806 Adress: VOLMINTA UG Ahornweg 7 Postal Code 06384 City Kirchwald Country: Germany Email: info@volminta-example.com
the design can be colored but doesnt have to be
Industry/Entity Type
Manufacturing and international distribution
Requirements
Must have
- show that we are a international company with headquater in Germany. our company infos and logo

```html
<!DOCTYPE html>
<html lang="en">
<head>
<meta charset="utf-8">
<title>VOLMINTA Letterhead</title>
<link rel="stylesheet" href="https://fonts.googleapis.com/css2?family=Saira:wght@300;400;600&display=swap">
<style>
  :root {
    --paper: #ffffff;
    --band: #dadcdb;
    --ink: #2b2a29;
    --rule: #c8c8c8;
    --footer-band: #72716f;
    --watermark: #f4f4f4;
  }
  html, body {
    margin: 0;
    padding: 0;
    overflow: hidden;
    background: var(--paper);
  }
  .letterhead {
    position: relative;
    width: 919px;
    height: 1200px;
    background: var(--paper);
    overflow: hidden;
    font-family: "Saira", sans-serif;
    color: var(--ink);
  }
  .header-block-left {
    position: absolute;
    left: 0; top: 43px;
    width: 60px; height: 70px;
    background: var(--band);
  }
  .brand {
    position: absolute;
    left: 78px; top: 43px;
    height: 70px;
    display: flex;
    align-items: center;
    gap: 10px;
  }
  .brand-dot {
    width: 30px; height: 30px;
    border-radius: 50%;
    background: var(--ink);
  }
  .brand-name {
    font-weight: 400;
    font-size: 34px;
    letter-spacing: 0.5px;
    color: var(--ink);
  }
  .header-contact {
    position: absolute;
    left: 354px; top: 43px;
    width: 565px; height: 70px;
    box-sizing: border-box;
    background: var(--band);
    padding: 9px 33px 0 0;
    text-align: right;
    font-size: 15.5px;
    font-weight: 300;
    line-height: 26px;
    white-space: nowrap;
  }
  .label { font-weight: 600; }
  .watermark {
    position: absolute;
    left: 670px; top: 346px;
    width: 392px; height: 392px;
    border-radius: 50%;
    background: var(--watermark);
  }
  .footer-details {
    position: absolute;
    left: 0; right: 0; top: 1094px;
    text-align: center;
    font-size: 14.5px;
    font-weight: 300;
    line-height: 26px;
    white-space: nowrap;
  }
  .footer-rule {
    position: absolute;
    left: 0; right: 0; top: 1154px;
    height: 2px;
    background: var(--rule);
  }
  .footer-band {
    position: absolute;
    left: 0; right: 0; top: 1160px;
    height: 40px;
    background: var(--footer-band);
  }
</style>
</head>
<body>
  <main class="letterhead">
    <div class="watermark" aria-hidden="true"></div>

    <div class="header-block-left"></div>
    <div class="brand">
      <span class="brand-dot" aria-hidden="true"></span>
      <span class="brand-name">VOLMINTA</span>
    </div>
    <div class="header-contact">
      <div><span class="label">Address :</span> VOLMINTA UG Ahornweg 7 Postal Code 06384</div>
      <div>City Kirchwald Country : Germany &nbsp;|&nbsp; <span class="label">Email :</span> info@volminta-example.com</div>
    </div>

    <div class="footer-details">
      <div><span class="label">VAT TAX :</span>&nbsp; DE5470318 <span class="label">Bank Account :</span> Kestrel Bank IBAN DE412058731ß204683</div>
      <div><span class="label">Swift :</span> MORV0417352 EORI 3150428697 <span class="label">Company Number :</span> HRB 51806</div>
    </div>
    <div class="footer-rule"></div>
    <div class="footer-band"></div>
  </main>
</body>
</html>
```